New Candy Packaging Design

Looking to create an attractive design for modern retail for our single stick candy that will stand out on retail shelves. It will be hung from a whole. The design should have brand elements like the irregular shapes, bright pastel colors. Please visit plumcrestcandyworks.com to ensure the product could be an extension of the product range. 3 colors, pink(sakura flavor), green(muscat grape flavor), and blue(french vanilla flavor).

Target Market(s)

Millenias and Genz

Industry/Entity Type

Food

Requirements
Must have
• Look and feel of brand extension for Tindra, Matt finish
Nice to have
• fruit shapes
Should not have
• tacky design

```html
<!DOCTYPE html>
<html lang="en">
<head>
<meta charset="utf-8">
<title>Tindra Rock Sugar Sticks – Packaging</title>
<link rel="stylesheet" href="https://fonts.googleapis.com/css2?family=Arvo:wght@400;700&display=swap">
<style>
  :root {
    --canvas: #f3f1ee;
    --ink: #222222;
    --white: #ffffff;
    --sakura: #c41f78;
    --sakura-deep: #a3145f;
    --sakura-soft: #dc4a6e;
    --muscat: #82b03c;
    --muscat-deep: #3f6a22;
    --muscat-soft: #b4d46a;
    --vanilla: #2f6494;
    --vanilla-deep: #24527d;
    --brand-pink: #cf4e9e;
  }
  * { margin: 0; padding: 0; box-sizing: border-box; }
  html, body { width: 1200px; height: 1170px; overflow: hidden; background: var(--canvas); }
  .canvas { position: relative; width: 1200px; height: 1170px; font-family: "Arvo", serif; }
  .variant-label {
    position: absolute; top: 138px; width: 60px; text-align: center;
    font-family: Arial, Helvetica, sans-serif; font-size: 30px; color: var(--ink);
  }
  .pack { position: absolute; top: 179px; width: 243px; height: 777px; }
  .pack svg { display: block; width: 100%; height: 100%; overflow: visible; }
  .pack text { font-family: "Arvo", serif; fill: var(--white); }
  .brand-corner {
    position: absolute; right: 36px; bottom: 32px; text-align: right;
    font-family: "Arvo", serif; color: var(--brand-pink); line-height: 1;
  }
  .brand-corner-tag { display: block; font-size: 11px; margin-right: 56px; margin-bottom: 2px; }
  .brand-corner-name { display: block; font-weight: 700; font-size: 46px; }
</style>
</head>
<body>
<main class="canvas">

  <div class="variant-label" style="left:219px">A</div>
  <div class="variant-label" style="left:558px">B</div>
  <div class="variant-label" style="left:900px">C</div>

  <!-- Sakura -->
  <section class="pack pack-sakura" style="left:126px">
    <svg viewBox="0 0 243 777" aria-label="Sakura flavor pack">
      <defs>
        <linearGradient id="sakuraPattern" x1="0" y1="0" x2="0" y2="1">
          <stop offset="0" stop-color="#d73d6c" stop-opacity="0.85"/>
          <stop offset="1" stop-color="#d73d6c" stop-opacity="0.35"/>
        </linearGradient>
        <linearGradient id="sakuraCandy" x1="0" y1="0" x2="0" y2="1">
          <stop offset="0" stop-color="#f3c3c4"/>
          <stop offset="0.75" stop-color="#eba4a4"/>
          <stop offset="1" stop-color="#d9b58e"/>
        </linearGradient>
        <linearGradient id="sakuraBloom" x1="0" y1="0" x2="0" y2="1">
          <stop offset="0" stop-color="#9c1355" stop-opacity="0"/>
          <stop offset="0.5" stop-color="#9c1355" stop-opacity="0.45"/>
          <stop offset="1" stop-color="#9c1355" stop-opacity="0"/>
        </linearGradient>
      </defs>
      <rect class="pack-top-seal" x="0" y="0" width="243" height="60" fill="var(--sakura-deep)"/>
      <path class="pack-body" d="M0 60 L14 72 L14 705 L0 720 L0 777 L243 777 L243 720 L229 705 L229 72 L243 60 Z" fill="var(--sakura)"/>
      <circle class="hang-hole" cx="121" cy="25" r="12" fill="var(--canvas)"/>
      <rect role="img" aria-label="Cluster of irregular blossom shapes with dotted, striped and lattice fills" x="16" y="62" width="211" height="168" rx="10" fill="url(#sakuraPattern)"/>
      <rect role="img" aria-label="Close-up photo of a cherry blossom" x="14" y="520" width="215" height="190" fill="url(#sakuraBloom)"/>
      <rect role="img" aria-label="Window showing a pink rock sugar candy on a wooden stick" x="66" y="303" width="110" height="390" rx="55" fill="url(#sakuraCandy)"/>
      <text x="145" y="112" font-size="10" text-anchor="middle">Rock Sugar Sticks</text>
      <text class="brand-name" x="121" y="158" font-size="50" font-weight="700" text-anchor="middle">Tindra</text>
      <text x="121" y="260" font-size="30" font-weight="700" text-anchor="middle">SAKURA</text>
      <text x="121" y="292" font-size="22" font-weight="700" text-anchor="middle">FLAVOR</text>
      <path id="sakuraArc" d="M35 700 Q121 725 207 700" fill="none"/>
      <text font-size="16"><textPath href="#sakuraArc" startOffset="50%" text-anchor="middle">A TREAT &amp; MORE</textPath></text>
    </svg>
  </section>

  <!-- Muscat grape -->
  <section class="pack pack-muscat" style="left:465px">
    <svg viewBox="0 0 243 777" aria-label="Muscat grape flavor pack">
      <defs>
        <linearGradient id="grapePhoto" x1="0" y1="0" x2="0" y2="1">
          <stop offset="0" stop-color="#9cc24e"/>
          <stop offset="0.6" stop-color="#a8cb5a"/>
          <stop offset="1" stop-color="#6f9a2e"/>
        </linearGradient>
        <linearGradient id="grapePattern" x1="0" y1="0" x2="0" y2="1">
          <stop offset="0" stop-color="#b8d86c" stop-opacity="0.85"/>
          <stop offset="1" stop-color="#b8d86c" stop-opacity="0.4"/>
        </linearGradient>
        <linearGradient id="grapeCandy" x1="0" y1="0" x2="0" y2="1">
          <stop offset="0" stop-color="#e6f0c2"/>
          <stop offset="0.75" stop-color="#d3e6a0"/>
          <stop offset="1" stop-color="#c9c08a"/>
        </linearGradient>
      </defs>
      <rect x="0" y="0" width="243" height="60" fill="var(--muscat-deep)"/>
      <path d="M0 60 L14 72 L14 705 L0 720 L0 777 L243 777 L243 720 L229 705 L229 72 L243 60 Z" fill="var(--muscat)"/>
      <rect role="img" aria-label="Photo of a bunch of green muscat grapes" x="14" y="230" width="215" height="547" fill="url(#grapePhoto)" opacity="0.8"/>
      <circle cx="121" cy="25" r="12" fill="var(--canvas)"/>
      <rect role="img" aria-label="Cluster of irregular grape shapes with clover, dot and stripe fills" x="20" y="52" width="205" height="162" rx="10" fill="url(#grapePattern)"/>
      <rect role="img" aria-label="Window showing a pale green rock sugar candy on a wooden stick" x="66" y="304" width="110" height="392" rx="55" fill="url(#grapeCandy)"/>
      <text x="121" y="110" font-size="10" text-anchor="middle">Rock Sugar Sticks</text>
      <text x="121" y="156" font-size="50" font-weight="700" text-anchor="middle">Tindra</text>
      <text x="121" y="235" font-size="20" text-anchor="middle">MUSCAT</text>
      <text x="121" y="268" font-size="32" font-weight="700" text-anchor="middle">GRAPE</text>
      <text x="121" y="297" font-size="22" font-weight="700" text-anchor="middle">FLAVOR</text>
      <path id="muscatArc" d="M35 706 Q121 728 207 712" fill="none"/>
      <text font-size="16"><textPath href="#muscatArc" startOffset="50%" text-anchor="middle">A TREAT &amp; MORE</textPath></text>
    </svg>
  </section>

  <!-- French vanilla -->
  <section class="pack pack-vanilla" style="left:809px">
    <svg viewBox="0 0 243 777" aria-label="French vanilla flavor pack">
      <defs>
        <linearGradient id="vanillaCandy" x1="0" y1="0" x2="0" y2="1">
          <stop offset="0" stop-color="#3f8fe0"/>
          <stop offset="0.75" stop-color="#2b78d4"/>
          <stop offset="1" stop-color="#c9ab84"/>
        </linearGradient>
        <linearGradient id="vanillaPhoto" x1="0" y1="0" x2="0" y2="1">
          <stop offset="0" stop-color="#e9e4d2" stop-opacity="0.15"/>
          <stop offset="0.5" stop-color="#e9e4d2" stop-opacity="0.45"/>
          <stop offset="1" stop-color="#e9e4d2" stop-opacity="0.15"/>
        </linearGradient>
      </defs>
      <rect x="0" y="0" width="243" height="60" fill="var(--vanilla-deep)"/>
      <path d="M0 60 L14 72 L14 705 L0 720 L0 777 L243 777 L243 720 L229 705 L229 72 L243 60 Z" fill="var(--vanilla)"/>
      <circle cx="121" cy="25" r="12" fill="var(--canvas)"/>
      <rect role="img" aria-label="Vanilla pods with a white vanilla flower" x="17" y="155" width="206" height="72" rx="8" fill="url(#vanillaPhoto)"/>
      <rect role="img" aria-label="White vanilla flowers" x="85" y="669" width="144" height="108" rx="8" fill="url(#vanillaPhoto)"/>
      <rect role="img" aria-label="Window showing a blue rock sugar candy on a wooden stick" x="71" y="298" width="100" height="397" rx="50" fill="url(#vanillaCandy)"/>
      <text x="142" y="111" font-size="10" text-anchor="middle">Rock Sugar Sticks</text>
      <text x="121" y="157" font-size="50" font-weight="700" text-anchor="middle">Tindra</text>
      <path id="vanillaArc" d="M95 552 A80 150 0 0 1 112 270" fill="none"/>
      <text font-size="17"><textPath href="#vanillaArc" startOffset="50%" text-anchor="middle">FRENCH <tspan font-weight="700" font-size="22">VANILLA</tspan> FLAVOR</textPath></text>
      <text x="0" y="0" font-size="17" text-anchor="middle" transform="translate(192 426) rotate(-80)">A TREAT &amp; MORE</text>
    </svg>
  </section>

  <div class="brand-corner">
    <span class="brand-corner-tag">Rock Sugar Sticks</span>
    <span class="brand-corner-name">Tindra</span>
  </div>

</main>
</body>
</html>
```